Business Card Design & Gift cards, Gift Cert, Donation Card

Retail Gift Store-in addition to Business Cards we'd like sequenced 2 sided Gift cards, Gift Certificate Cards, and Donation Cards.please see examples and email for clarificationlogos attached with examples-
Gift Card, Gift Certificate and Donation Card will all be same style just differant upper right title, with back side info as example.
business card, as example is single sided.
looking for additional ideas for layout

Industry/Entity Type

Business

Contact Information for Business Card

211 Newman St.East Tawas, MI 48730989.362.8730Office@BrewKrew.com

Requirements
Must have
• Blue as per example
• Logos provided
• like gradiant background

```html
<!DOCTYPE html>
<html lang="en">
<head>
<meta charset="utf-8">
<title>Tillow Marsh – Business Card</title>
<link href="https://fonts.googleapis.com/css2?family=Patrick+Hand&display=swap" rel="stylesheet">
<style>
  :root {
    --page-bg: #1b1b1b;
    --royal-blue: #0230cc;
    --sky-top: #8ec6f2;
    --sky-mid: #c4e1f8;
    --sky-bottom: #f8fbfe;
    --ink: #111111;
    --sun-yellow: #f5e11a;
    --white: #ffffff;
  }
  * { margin: 0; padding: 0; box-sizing: border-box; }
  html, body {
    width: 1189px; height: 1200px; overflow: hidden;
    background: var(--page-bg);
    font-family: "Patrick Hand", "Comic Sans MS", cursive;
  }
  .card {
    position: absolute; left: 140px; width: 917px; height: 522px; overflow: hidden;
  }
  .card--front { top: 45px; }
  .card--back {
    top: 623px;
    background: linear-gradient(to bottom, var(--sky-top) 0%, var(--sky-mid) 45%, var(--sky-bottom) 100%);
  }
  .card__backdrop { position: absolute; inset: 0; width: 917px; height: 522px; }
  .brand-name {
    position: absolute; color: var(--royal-blue); font-weight: 400; white-space: nowrap;
    line-height: 1; letter-spacing: 1px;
  }
  .card--front .brand-name { left: 200px; top: 92px; font-size: 88px; }
  .card--back .brand-name { left: 80px; top: 196px; font-size: 150px; }
  .illustration { position: absolute; border-radius: 40% 40% 8px 8px; }
  .card--front .illustration {
    left: 43px; top: 192px; width: 298px; height: 306px;
    background: linear-gradient(to bottom, rgba(2,48,204,0.75) 0%, rgba(2,48,204,0.55) 60%, rgba(245,225,26,0.8) 100%);
  }
  .card--back .illustration {
    left: 2px; top: 18px; width: 470px; height: 498px;
    background: linear-gradient(to bottom, rgba(2,48,204,0.16) 0%, rgba(2,48,204,0.12) 65%, rgba(245,225,26,0.22) 100%);
  }
  .contact-list {
    position: absolute; right: 180px; top: 290px; list-style: none;
    color: var(--ink); font-size: 25px; line-height: 1.5; letter-spacing: 1px;
  }
  .contact-list li { display: flex; justify-content: flex-end; align-items: flex-start; gap: 0; }
  .contact-item__text { text-align: right; }
  .contact-item__icon {
    position: absolute; right: -42px; width: 20px; height: 20px; margin-top: 8px;
    background: var(--royal-blue); display: flex; align-items: center; justify-content: center;
  }
  .contact-item { position: relative; }
  .contact-item--address .contact-item__text { line-height: 1.3; padding-top: 2px; }
</style>
</head>
<body>

<section class="card card--front" aria-label="Business card front">
  <svg class="card__backdrop" viewBox="0 0 917 522" aria-hidden="true">
    <defs>
      <linearGradient id="skyFade" x1="0" y1="0" x2="0" y2="1">
        <stop offset="0" stop-color="#8ec6f2"/>
        <stop offset="0.55" stop-color="#c4e1f8"/>
        <stop offset="1" stop-color="#f8fbfe"/>
      </linearGradient>
    </defs>
    <rect width="917" height="522" fill="#0230cc"/>
    <ellipse cx="458" cy="262" rx="492" ry="224" fill="url(#skyFade)" stroke="#ffffff" stroke-width="3"/>
  </svg>

  <div class="brand-name">Tillow Marsh</div>

  <div class="illustration" role="img" aria-label="Illustration of a dancing figure stepping over a rising sun on a wave line"></div>

  <ul class="contact-list">
    <li class="contact-item">
      <span class="contact-item__text">989.517.4296</span>
      <span class="contact-item__icon">
        <svg width="14" height="12" viewBox="0 0 14 12" aria-hidden="true"><path d="M1 4 Q7 -1 13 4 L11 5.5 L9.5 3.5 L4.5 3.5 L3 5.5 Z M3.5 6 L10.5 6 L11.5 11 L2.5 11 Z" fill="#fff"/></svg>
      </span>
    </li>
    <li class="contact-item">
      <span class="contact-item__text">Office@TillowMarsh.com</span>
      <span class="contact-item__icon">
        <svg width="14" height="10" viewBox="0 0 14 10" aria-hidden="true"><rect x="0.5" y="0.5" width="13" height="9" fill="none" stroke="#fff"/><path d="M0.5 0.5 L7 6 L13.5 0.5" fill="none" stroke="#fff"/></svg>
      </span>
    </li>
    <li class="contact-item contact-item--address">
      <span class="contact-item__text">482 Larkfield Ave.<br>Harlow Bay, MI 48611</span>
      <span class="contact-item__icon">
        <svg width="10" height="14" viewBox="0 0 10 14" aria-hidden="true"><path d="M5 13 L1.3 6.5 A4 4 0 1 1 8.7 6.5 Z" fill="#fff"/><circle cx="5" cy="4.8" r="1.5" fill="#0230cc"/></svg>
      </span>
    </li>
  </ul>
</section>

<section class="card card--back" aria-label="Business card back">
  <div class="illustration" role="img" aria-label="Faint decorative illustration of a dancing figure over a rising sun"></div>
  <div class="brand-name">Tillow Marsh</div>
</section>

</body>
</html>
```